Business Card Design

New business card design

Target Market(s)

Residential & Commercial Property Managers

Industry/Entity Type

Plumbing Services

Contact Information for Business Card

Name - Rowan Keddle, title - Director, Phone Number - 0431 286 517, email - rowan@tbk-plumbing.com.au, Company ABN - 73 215 904 386,

Font styles to use
Sans Serif

Colors
0054AA
0677BA
7BADD7
CADEEF
E8F1F8

```html
<!DOCTYPE html>
<html lang="en">
<head>
<meta charset="utf-8">
<title>TBK Plumbing Services – Business Card</title>
<link rel="stylesheet" href="https://fonts.googleapis.com/css2?family=Montserrat:wght@300;400;500;700&display=swap">
<style>
  :root {
    --backdrop: #e6e3de;
    --card-light: #ffffff;
    --card-dark: #1d232d;
    --ink: #1d232d;
    --ink-soft: #2a2f38;
    --drop-blue: #2aa6df;
    --on-dark: #ffffff;
  }
  * { box-sizing: border-box; margin: 0; padding: 0; }
  html, body {
    width: 900px; height: 1200px; overflow: hidden;
    background: var(--backdrop);
    font-family: "Montserrat", Arial, sans-serif;
    color: var(--ink);
  }
  .canvas { position: relative; width: 900px; height: 1200px; }
  .card {
    position: absolute;
    width: 742px; height: 441px;
    border-radius: 22px;
    box-shadow: 0 6px 18px rgba(0,0,0,0.25);
  }
  .card-front { left: 80px; top: 131px; background: var(--card-light); }
  .card-back { left: 79px; top: 638px; height: 442px; background: var(--card-dark); }

  .brand {
    display: flex; align-items: center; gap: 14px;
    font-weight: 300; white-space: nowrap;
  }
  .card-front .brand {
    position: absolute; left: 36px; top: 80px;
    font-size: 32px; letter-spacing: 1px; color: var(--ink);
  }
  .brand-dot {
    width: 18px; height: 18px; border-radius: 50%;
    background: var(--drop-blue); flex: none;
  }
  .card-back .brand {
    position: absolute; left: 0; right: 0; top: 190px;
    justify-content: center;
    font-size: 46px; letter-spacing: 2px; color: var(--on-dark);
  }
  .card-back .brand-dot { width: 24px; height: 24px; }

  .holder { position: absolute; right: 45px; top: 46px; text-align: right; }
  .holder-name { font-size: 25px; font-weight: 700; line-height: 1.2; }
  .holder-title { font-size: 15px; font-weight: 400; margin-top: 2px; }

  .address {
    position: absolute; left: 39px; top: 216px;
    font-size: 16px; line-height: 20px; font-weight: 400;
  }
  .contacts {
    position: absolute; left: 39px; top: 284px;
    list-style: none; font-size: 15.5px; font-weight: 400;
  }
  .contacts li { display: flex; align-items: center; gap: 11px; height: 31px; }
  .contacts svg { width: 17px; height: 17px; fill: var(--ink); flex: none; }
  .abn {
    position: absolute; left: 39px; top: 384px;
    font-size: 15.5px; font-weight: 400;
  }
  .abn strong { font-weight: 700; }
</style>
</head>
<body>
<main class="canvas">
  <section class="card card-front" aria-label="Business card front">
    <div class="brand"><span class="brand-dot"></span>TBK Plumbing Services</div>

    <div class="holder">
      <p class="holder-name">Rowan Keddle</p>
      <p class="holder-title">Director</p>
    </div>

    <p class="address">48 Harrow Creek Road<br>Brookvale, NSW 2100</p>

    <ul class="contacts">
      <li>
        <svg viewBox="0 0 24 24" aria-hidden="true"><path d="M6.6 10.8a15.1 15.1 0 0 0 6.6 6.6l2.2-2.2a1 1 0 0 1 1-.25 11.4 11.4 0 0 0 3.6.57 1 1 0 0 1 1 1V20a1 1 0 0 1-1 1A17 17 0 0 1 3 4a1 1 0 0 1 1-1h3.5a1 1 0 0 1 1 1c0 1.25.2 2.45.57 3.57a1 1 0 0 1-.25 1z"/></svg>
        0431 286 517
      </li>
      <li>
        <svg viewBox="0 0 24 24" aria-hidden="true"><path d="M3 5h18v14H3z M4.5 6.5 12 12l7.5-5.5v-.2H4.5z" fill-rule="evenodd"/><path d="M3 5h18v2l-9 6-9-6z" fill="#fff" opacity="0"/></svg>
        rowan@tbk-plumbing.com.au
      </li>
      <li>
        <svg viewBox="0 0 24 24" aria-hidden="true"><path d="M12 2a10 10 0 1 0 0 20 10 10 0 0 0 0-20zm-1 17.9A8 8 0 0 1 4.2 10.2L9 15v1a2 2 0 0 0 2 2zm6.9-2.5A2 2 0 0 0 16 16h-1v-3a1 1 0 0 0-1-1H8v-2h2a1 1 0 0 0 1-1V7h2a2 2 0 0 0 2-2v-.4a8 8 0 0 1 2.9 12.8z"/></svg>
        www.tbk-plumbing.com.au
      </li>
    </ul>

    <p class="abn"><strong>ABN</strong> - 73 215 904 386</p>
  </section>

  <section class="card card-back" aria-label="Business card back">
    <div class="brand"><span class="brand-dot"></span>TBK Plumbing Services</div>
  </section>
</main>
</body>
</html>
```